Valdo Capital

We need a corporate style website design for a new company based in Shenzhen's Qianhai Special Economic Development Zone, China. We provide a range of financial services to large international investment companies. Typically these companies invest over 5 million RMB. The company is part of a group that consists of NorthKilns, ValdoTrusts and ValdoEquity. Our location and gateway into Qianhai Special Economic Zone is our core advantage. We would like to see designs that Do Not use purple and orange. The website design should be similar to other websites in this family but different enough to give it a unique style (See attached website links for reference). The final design should communicate financial safety and growth. This website will act partly as a business chamber with connections to the government so we would like it to be diplomatic in style.

www.northkilns.example
www.valdotrusts.example

*Nevegation Bar
Should including Homepage, Financial Product, Team, News.
Could refer to www.valdotrusts.example

*Contact Details

Miss Lan
Address:E 728, North Block, KMO Centre, East Sector, Shenzhen Bright Science Campus
Telephone: +86 0755 63920417
Cellphone: +86 13957280316

* Social Media
Should be grouped like:
1. Weibo QRcode+ Weibo
2. Facebook, Twitter, Linkedin.

Industry/Entity Type

Investment

```html
<!DOCTYPE html>
<html lang="en">
<head>
<meta charset="utf-8">
<title>Valdo Capital</title>
<link href="https://fonts.googleapis.com/css2?family=Open+Sans:wght@300;400;600;700&family=Ubuntu:ital,wght@0,300;0,400;0,500;1,300;1,400&display=swap" rel="stylesheet">
<style>
:root{
  --bar:#2b2b2b;
  --band:#232323;
  --footer:#2e2e2e;
  --accent:#2aa4dc;
  --ink:#333333;
  --muted:#8a8a8a;
  --soft:#a8a8a8;
  --line:#dddddd;
  --white:#ffffff;
}
*{margin:0;padding:0;box-sizing:border-box}
html,body{width:1158px;height:1200px;overflow:hidden;background:var(--white)}
body{position:relative;font-family:"Ubuntu",sans-serif;color:var(--ink)}
.abs{position:absolute}

.topbar{left:0;top:0;width:1158px;height:53px;background:var(--bar);z-index:2}
.brand{left:106px;top:0;width:319px;height:94px;background:var(--white);z-index:3;display:flex;align-items:center;padding-left:20px;gap:14px}
.brand-mark{width:40px;height:40px;background:#1f7fae}
.brand-name{font-family:"Open Sans",sans-serif;font-weight:600;font-size:27px;color:#1c1c1c;letter-spacing:.5px}
.nav{right:106px;top:0;height:53px;display:flex;align-items:center;gap:30px;font-size:12.5px;font-weight:500;color:#d0d0d0;z-index:3}
.nav a{color:inherit;text-decoration:none;text-transform:uppercase}
.nav a.active{color:var(--accent)}
.nav .divider{width:1px;height:20px;background:#666;margin-right:-12px}

.hero{left:0;top:53px;width:1158px;height:630px;background:linear-gradient(180deg,#0a0d18 0%,#1b1e2c 35%,#4b3a26 62%,#2a2440 78%,#1a1c5a 92%,#0e1030 100%)}
.hero-copy{left:107px;top:282px;width:470px;color:var(--white);font-family:"Open Sans",sans-serif}
.hero-copy h1{font-weight:300;font-size:60px;line-height:58px;letter-spacing:-1.5px}
.hero-copy h1 strong{display:block;font-weight:600;letter-spacing:-1px}
.hero-copy p{margin-top:14px;margin-left:4px;font-size:16px;line-height:21.5px;letter-spacing:-.2px}
.hero-copy .more{display:inline-block;margin-top:8px;margin-left:4px;font-size:16.5px;color:var(--white);text-decoration:underline}
.hero-copy .more::after{content:"";display:inline-block;margin-left:6px;border-left:4px solid #ddd;border-top:3px solid transparent;border-bottom:3px solid transparent;vertical-align:middle}

.services{left:0;top:683px;width:1158px;height:74px;background:var(--band)}
.service{top:0;width:218px;height:74px;padding:8px 0 0 0;border-right:1px solid #3d3d3d}
.service.current::before{content:"";position:absolute;left:0;top:0;width:218px;height:3px;background:var(--accent)}
.service h3{font-weight:400;font-size:20px;color:var(--white);letter-spacing:.2px}
.service p{font-size:12.5px;line-height:17.5px;color:#8c8c8c;font-weight:300;margin-top:1px;padding-left:1px}

.col-title{top:791px;font-family:"Open Sans",sans-serif;font-weight:600;font-size:21.5px;color:#2d2d2d}

.news-item{left:107px;width:275px;font-size:12px;line-height:18.5px;color:var(--muted)}
.news-item .head{white-space:nowrap}
.news-item .blue{color:var(--accent)}
.news-item .date{font-style:italic;color:var(--accent);white-space:nowrap}
.news-item p{margin-top:9px;padding-left:2px;width:270px}
.rule{left:107px;top:956px;width:262px;height:1px;background:var(--line)}

.view-all{top:1080px;font-style:italic;font-size:15px;color:#333}

.post{left:435px;width:300px;height:98px}
.thumb-frame{left:0;top:0;width:98px;height:98px;border:1px solid var(--line);background:var(--white);padding:8px}
.thumb{width:80px;height:80px}
.post-text{left:107px;top:8px;width:180px;font-size:13.5px;line-height:20.5px;color:#555}
.post-date{left:107px;top:63px;display:flex;align-items:center;gap:9px;font-size:9.5px;color:#999}

.quote-box{left:758px;top:843px;width:296px;height:144px;border:1px solid #d6d6d6;background:var(--white)}
.quote-box p{position:absolute;left:25px;top:30px;width:260px;font-size:13px;line-height:19.5px;color:#555}
.quote-mark{position:absolute;font-family:"Open Sans",sans-serif;font-size:30px;color:#c5c5c5;line-height:1}
.quote-tail{left:780px;top:986px;width:18px;height:10px}
.avatar{left:762px;top:1001px;width:60px;height:60px;border-radius:50%;background:radial-gradient(circle at 50% 40%,#d9b48e,#8a6a4c 70%,#3a3a3a)}
.person{left:829px;top:1009px;font-size:14px;line-height:20px}
.person .name{color:var(--accent)}
.person .role{color:#555}

.footer{left:0;top:1143px;width:1158px;height:57px;background:var(--footer)}
.copyright{left:106px;top:1163px;font-size:12.5px;color:#b5b5b5;font-weight:300}
.social{left:946px;top:1157px;display:flex;gap:11px}
.social span{width:28px;height:28px;border-radius:50%;background:#5a5a5a;display:block}
</style>
</head>
<body>

<header class="abs topbar"></header>
<div class="abs brand">
  <span class="brand-mark"></span>
  <span class="brand-name">Valdo Capital</span>
</div>
<nav class="abs nav">
  <a href="#" class="active">Home</a>
  <a href="#">Financial Products</a>
  <a href="#">Team</a>
  <a href="#">News</a>
  <span class="divider"></span>
  <svg width="20" height="20" viewBox="0 0 20 20" aria-label="Search"><circle cx="8" cy="8" r="6" fill="none" stroke="#8a8a8a" stroke-width="2"/><line x1="12.5" y1="12.5" x2="18" y2="18" stroke="#8a8a8a" stroke-width="2.4" stroke-linecap="round"/></svg>
</nav>

<section class="abs hero" role="img" aria-label="Night skyline of a riverside city with illuminated towers and a brightly lit boat on the water"></section>
<div class="abs hero-copy">
  <h1>Welcome To <strong>Valdo Capital</strong></h1>
  <p>Lorem ipsum dolor sit amet, consectetur adipisicing elit, sed do eiusmod tempor incididunt ut labore et dolore magna aliqua..</p>
  <a href="#" class="more">Read More</a>
</div>

<section class="abs services">
  <div class="abs service current" style="left:106px"><h3>Finance</h3><p>Lorem ipsum dolor sit amet, consec<br>adipisicing elit..</p></div>
  <div class="abs service" style="left:343px"><h3>Consultancy</h3><p>Lorem ipsum dolor sit amet, consec<br>adipisicing elit..</p></div>
  <div class="abs service" style="left:580px"><h3>Insurance</h3><p>Lorem ipsum dolor sit amet, consec<br>adipisicing elit..</p></div>
  <div class="abs service" style="left:817px;border-right:none"><h3>Property Management</h3><p>Lorem ipsum dolor sit amet, consec<br>adipisicing elit..</p></div>
</section>

<h2 class="abs col-title" style="left:106px">News and Events</h2>
<h2 class="abs col-title" style="left:435px">Our Blog</h2>
<h2 class="abs col-title" style="left:756px">Testimonials</h2>

<article class="abs news-item" style="top:850px">
  <div class="head">Ross Hale Westmere Sauvignon <span class="blue">Blanced etc</span></div>
  <div class="date">posted on March 13, 2014 20:15</div>
  <p>Media release; summer has never tasted better than with Ross Hale's 2014 Sauvignon Blanc</p>
</article>
<div class="abs rule"></div>
<article class="abs news-item" style="top:977px">
  <div class="head">Ross Hale Westmere Sauvignon <span class="blue">Blanced etc</span></div>
  <div class="date">posted on March 13, 2014 20:15</div>
  <p>Media release; summer has never tasted better than with Ross Hale's 2012 Sauvignon Blanc</p>
</article>
<a class="abs view-all" style="left:110px">View All</a>

<article class="abs post" style="top:852px">
  <div class="abs thumb-frame"><div class="thumb" role="img" aria-label="Business team reviewing printed charts at a desk" style="background:linear-gradient(135deg,#e8eef5,#9fb3c8 60%,#3d4a5a)"></div></div>
  <div class="abs post-text">This in one of the important Blog Post of this website.</div>
  <div class="abs post-date"><svg width="14" height="13" viewBox="0 0 14 13"><rect x="1" y="2" width="12" height="10" fill="none" stroke="#aaa"/><line x1="1" y1="5" x2="13" y2="5" stroke="#aaa"/><line x1="4" y1="0" x2="4" y2="3" stroke="#aaa"/><line x1="10" y1="0" x2="10" y2="3" stroke="#aaa"/></svg>25, JAN, 2011</div>
</article>
<article class="abs post" style="top:970px">
  <div class="abs thumb-frame"><div class="thumb" role="img" aria-label="Business people in suits shaking hands" style="background:linear-gradient(135deg,#dfe3e8,#6c7680 55%,#262a30)"></div></div>
  <div class="abs post-text">This in one of the important Blog Post of this website.</div>
  <div class="abs post-date"><svg width="14" height="13" viewBox="0 0 14 13"><rect x="1" y="2" width="12" height="10" fill="none" stroke="#aaa"/><line x1="1" y1="5" x2="13" y2="5" stroke="#aaa"/><line x1="4" y1="0" x2="4" y2="3" stroke="#aaa"/><line x1="10" y1="0" x2="10" y2="3" stroke="#aaa"/></svg>25, JAN, 2011</div>
</article>
<a class="abs view-all" style="left:441px">View All</a>

<div class="abs quote-box">
  <span class="quote-mark" style="left:7px;top:6px">&ldquo;</span>
  <p>Lorem Ipsum is simply dummy text of the printing and typesetting industry. Lorem Ipsum has been the industry's standard dummy text ever since the 1500s, when</p>
  <span class="quote-mark" style="right:12px;bottom:-8px">&rdquo;</span>
</div>
<svg class="abs quote-tail" viewBox="0 0 18 10"><polygon points="0,0 18,0 9,9" fill="#fff" stroke="#d6d6d6"/><line x1="0" y1="0.5" x2="18" y2="0.5" stroke="#fff" stroke-width="2"/></svg>
<div class="abs avatar" role="img" aria-label="Portrait photo of the client"></div>
<div class="abs person"><div class="name">Clara Whitby</div><div class="role">Manager</div></div>
<a class="abs view-all" style="left:761px">View All</a>

<footer class="abs footer"></footer>
<div class="abs copyright">Copyright © 2014 Valdo Capital. All Rights Reserved</div>
<div class="abs social" aria-label="Social links"><span></span><span></span><span></span></div>

</body>
</html>
```